Business card for a new cabinet shop company named Veloran Cabinets for high end cabinets

Design a business card, thinking dark rich green with colours to speak of high end luxury ie; cream, gold, black possibly

Mitchell Tarrowby
Director Craftsman
Email: info@veloranjoinery-example.com.au
Instagram : @veloran.cabinets

```html
<!DOCTYPE html>
<html lang="en">
<head>
<meta charset="utf-8">
<title>Veloran Cabinets — Business Card</title>
<link rel="stylesheet" href="https://fonts.googleapis.com/css2?family=Jost:wght@400;500&family=Poppins:wght@400;500&display=swap">
<style>
  :root {
    --backdrop: #d4d4d4;
    --card-dark: #1e1e1e;
    --card-dark-soft: #242424;
    --card-light: #ffffff;
    --gold: #c8aa6a;
    --ink: #111111;
    --text-light: #f2f2f2;
  }
  * { box-sizing: border-box; margin: 0; padding: 0; }
  html, body {
    width: 1157px; height: 1200px; overflow: hidden;
    background: var(--backdrop);
  }
  .canvas { position: relative; width: 1157px; height: 1200px; }

  .card {
    position: absolute; left: 214px; width: 727px; height: 415px;
    box-shadow: 0 14px 26px rgba(0,0,0,0.28);
    overflow: hidden;
  }
  .card--front { top: 157px; background: var(--card-dark); }
  .card--back { top: 635px; background: var(--card-light); }

  .front-texture {
    position: absolute; inset: 0;
    background: radial-gradient(ellipse at center, var(--card-dark-soft) 0%, var(--card-dark) 75%);
  }

  .brand {
    position: absolute; left: 0; right: 0;
    display: flex; align-items: center; justify-content: center; gap: 22px;
  }
  .brand-square {
    width: 46px; height: 46px; border: 3px solid var(--gold);
  }
  .brand-name {
    font-family: "Poppins", sans-serif; font-weight: 500;
    font-size: 50px; letter-spacing: 1px; color: var(--gold);
    line-height: 1;
  }
  .card--front .brand { top: 180px; }
  .card--back .brand { top: 95px; }

  .back-band {
    position: absolute; left: 0; right: 0; top: 235px; bottom: 0;
    background: var(--card-dark);
    border-top: 4px solid var(--gold);
  }
  .person {
    position: absolute; right: 390px; top: 54px; text-align: right;
    font-family: "Jost", sans-serif;
  }
  .person-name { font-weight: 500; font-size: 33px; color: var(--gold); line-height: 1.1; white-space: nowrap; }
  .person-role { font-size: 17px; letter-spacing: 1.2px; color: var(--text-light); margin-top: 4px; }

  .divider {
    position: absolute; left: 364px; top: 46px; width: 2px; height: 78px;
    background: var(--gold);
  }
  .contacts {
    position: absolute; left: 389px; top: 44px; list-style: none;
    font-family: "Jost", sans-serif; font-size: 17.5px; letter-spacing: 0.4px;
    color: var(--text-light);
  }
  .contacts li { display: flex; align-items: center; gap: 10px; height: 30.5px; white-space: nowrap; }
  .contacts svg { width: 15px; height: 15px; flex: none; }
</style>
</head>
<body>
<main class="canvas">

  <section class="card card--front">
    <div class="front-texture" role="img" aria-label="Faint repeating monogram pattern in dark grey across the card"></div>
    <div class="brand">
      <span class="brand-square"></span>
      <span class="brand-name">Veloran Cabinets</span>
    </div>
  </section>

  <section class="card card--back">
    <div class="brand">
      <span class="brand-square"></span>
      <span class="brand-name">Veloran Cabinets</span>
    </div>

    <div class="back-band">
      <div class="person">
        <p class="person-name">Mitchell Tarrowby</p>
        <p class="person-role">Director Craftsman</p>
      </div>
      <span class="divider"></span>
      <ul class="contacts">
        <li>
          <svg viewBox="0 0 16 16" aria-hidden="true"><rect x="2" y="2" width="12" height="12" fill="none" stroke="var(--gold)" stroke-width="1.6"/></svg>
          @veloran.cabinets
        </li>
        <li>
          <svg viewBox="0 0 16 16" aria-hidden="true"><rect x="1" y="3.5" width="14" height="9" fill="var(--gold)"/><path d="M1 3.5 L8 9 L15 3.5" fill="none" stroke="var(--card-dark)" stroke-width="1.2"/></svg>
          info@veloranjoinery-example.com.au
        </li>
        <li>
          <svg viewBox="0 0 16 16" aria-hidden="true"><circle cx="8" cy="8" r="6.5" fill="none" stroke="var(--gold)" stroke-width="1.5"/><ellipse cx="8" cy="8" rx="2.6" ry="6.5" fill="none" stroke="var(--gold)" stroke-width="1.2"/><path d="M1.5 8 H14.5" stroke="var(--gold)" stroke-width="1.2"/></svg>
          veloranjoinery-example.com.au
        </li>
      </ul>
    </div>
  </section>

</main>
</body>
</html>
```